Judicial election website to attract voters

I need a simple one-page web design for a judicial election. I'm going to put up one picture, maybe two. The picture I have needs a little touch-up (whiten teeth for example). I have 3 paragraphs of text. I'd like a "Donate" button that can link to a CoinDrift account. I'd also like a little background design, like the Constitution or something like that. There's a couple other little things but that's the bulk of it.

Target Market(s)

Involved voters and some media

Industry/Entity Type

Legal

Number of Pages Required

1 page

Font styles to use
Sans Serif

Requirements
Must have
• My picture, text, donate button
• Phrase "Remember to vote August 30, 2016!"
Nice to have
• Perhaps a second photo, maybe a short 30 second video of me talking directly to the voters, cool background: Constitution, something judgey.
Should not have
• Not sure ... profanity, I guess.

```html
<!DOCTYPE html>
<html lang="en">
<head>
<meta charset="utf-8">
<title>Local Elections</title>
<link rel="stylesheet" href="https://fonts.googleapis.com/css2?family=Lato:wght@400;700&family=Raleway:wght@700&display=swap">
<style>
:root{
  --navy:#13206a;
  --red:#c0152a;
  --text:#4a4a4a;
  --rule:#9aa0b8;
  --white:#ffffff;
  --grey:#eeeef0;
  --black:#0a0a0a;
}
*{margin:0;padding:0;box-sizing:border-box}
html,body{width:772px;height:1200px;overflow:hidden;background:var(--white)}
body{font-family:'Lato',sans-serif;color:var(--text);position:relative}
.site-header{position:absolute;top:0;left:0;width:772px;height:62px;background:var(--white)}
.social{position:absolute;display:flex;gap:10px}
.social span{display:block;width:18px;height:18px;border-radius:3px;background:var(--navy)}
.site-header .social{left:63px;top:22px}
.brand{position:absolute;font-family:'Lato',sans-serif;font-weight:700;font-size:17px;letter-spacing:.5px;line-height:1;display:flex;align-items:center;gap:7px}
.brand i{display:block;width:10px;height:10px;background:currentColor}
.site-header .brand{left:336px;top:22px;color:var(--navy)}
.donate{position:absolute;width:96px;height:30px;display:flex;align-items:center;justify-content:center;gap:7px;color:var(--white);font-size:12px;letter-spacing:.5px;text-decoration:none}
.donate svg{width:15px;height:15px}
.site-header .donate{left:611px;top:16px;background:var(--navy);border-bottom:2px solid var(--red)}
.hero{position:absolute;top:62px;left:0;width:772px;height:309px;background:linear-gradient(110deg,#8d97a6 0%,#a4353f 30%,#d8d8da 50%,#b9b6b0 68%,#c79a80 85%,#e07c5a 100%)}
.vote-banner{position:absolute;left:62px;top:213px;width:380px;height:41px;background:var(--navy);border-left:4px solid var(--red);color:var(--white);font-weight:700;font-size:21px;line-height:41px;padding-left:13px}
.panel{position:absolute;width:386px;height:245px}
.photo{position:absolute;width:386px;height:245px}
.about{top:371px;left:0;background:var(--white);padding:28px 0 0 62px}
.video{top:371px;left:386px;background:radial-gradient(circle at 50% 50%,#e4e4e2 0 36%,#5a5a6a 55%,#2a2a3a 100%)}
.play{position:absolute;left:175px;top:104px;width:36px;height:36px;border-radius:50%;background:var(--white);display:flex;align-items:center;justify-content:center}
.ballot{top:615px;left:0;background:linear-gradient(100deg,#8e2a2c 0%,#f1efe9 35%,#2c3c6e 70%,#b13b38 100%)}
.ipsum-one{top:615px;left:386px;background:var(--grey);padding:28px 0 0 15px}
.ipsum-two{top:860px;left:0;background:var(--white);padding:28px 0 0 60px}
.tablet{top:860px;left:386px;background:linear-gradient(160deg,#c9444a 0%,#d8dbe4 25%,#eef0f5 60%,#b9bfcc 100%)}
h2{font-family:'Raleway',sans-serif;font-weight:700;font-size:20px;color:var(--navy);line-height:1;letter-spacing:.2px}
h2 em{font-style:normal;color:var(--red)}
.rule{width:305px;height:1px;background:var(--rule);margin:13px 0 13px;position:relative}
.rule::before{content:"";position:absolute;left:0;top:0;width:60px;height:1px;background:var(--red)}
p{font-size:8.6px;line-height:14px;width:308px;margin-bottom:5px}
.ipsum-two .rule{width:307px}
ul{list-style:none;margin-top:2px}
li{font-size:8.6px;line-height:20px;display:flex;align-items:center;gap:5px}
li svg{width:12px;height:10px;flex:none}
.site-footer{position:absolute;top:1105px;left:0;width:772px;height:67px;background:var(--navy)}
.site-footer .social{left:63px;top:25px}
.site-footer .social span{background:#3a4a9a}
.site-footer .brand{left:347px;top:25px;color:var(--white)}
.site-footer .donate{left:611px;top:19px;background:var(--red);border-bottom:2px solid var(--white)}
.copyright{position:absolute;top:1172px;left:0;width:772px;height:28px;background:var(--black);color:var(--white);font-size:8px;text-align:center;line-height:28px}
</style>
</head>
<body>
<header class="site-header">
  <div class="social" aria-label="Social links"><span></span><span></span><span></span><span></span></div>
  <div class="brand"><i></i>LOCAL ELECTIONS</div>
  <a class="donate" href="#" aria-label="Donate with CoinDrift"><svg viewBox="0 0 16 16"><circle cx="10" cy="5" r="4" fill="none" stroke="#fff" stroke-width="1.4"/><path d="M1 14 L5 10 H10 L12 12" fill="none" stroke="#fff" stroke-width="1.4"/></svg>DONATE</a>
</header>

<section class="hero" role="img" aria-label="Waving American flag before the Capitol dome, with the smiling candidate on the right">
  <div class="vote-banner">Remember To Vote August 30, 2016!</div>
</section>

<section class="panel about">
  <h2>ABOUT <em>ME</em></h2>
  <div class="rule"></div>
  <p>Lorem ipsum dolor sit amet, consectetuer adipiscing elit, sed diam nonummy nibh euismod tincidunt ut laoreet dolore magna aliquam erat volutpat. Ut wisi enim ad minim veniam, quis nostrud exerci tation ullamcorper suscipit lobortis nisl ut aliquip ex ea commodo consequat. Duis autem vel eum iriure dolor in hendrerit in vulputate velit esse molestie consequat, vel illum dolore eu feugiat nulla facilisis at vero eros et accumsan et iusto odio dignissim qui blandit praesent luptatum zzril delenit augue duis dolore te feugait nulla facilisi.</p>
  <p>Lusto odio dignissim qui blandit praesent luptatum zzrileti delenit augue duis dolore teleoi feugait nulla dolor in hendrerit in vulputate consequat.Duis autem vel eum iriure dolor in hendrerit in vulputate.</p>
</section>

<section class="photo video" role="img" aria-label="Video still: hands holding an Elections 2016 sign">
  <div class="play"><svg width="14" height="14" viewBox="0 0 14 14"><path d="M3 1 L12 7 L3 13 Z" fill="#111"/></svg></div>
</section>

<section class="photo ballot" role="img" aria-label="Hand placing an official ballot into a ballot box before a flag"></section>

<section class="panel ipsum-one">
  <h2>LOREM <em>IPSUM</em></h2>
  <div class="rule"></div>
  <p>Lorem ipsum dolor sit amet, consectetuer adipiscing elit, sed diam nonummy nibh euismod tincidunt ut laoreet dolore magna aliquam erat volutpat. Ut wisi enim ad minim veniam, quis nostrud exerci tation ullamcorper suscipit lobortis nisl ut aliquip ex ea commodo consequat. Duis autem vel eum iriure dolor in hendrerit in vulputate velit esse molestie consequat, vel illum dolore eu feugiat nulla facilisis at vero eros et accumsan et iusto odio dignissim qui blandit praesent luptatum zzril delenit augue duis dolore te feugait nulla facilisi.</p>
  <p>Lusto odio dignissim qui blandit praesent luptatum zzrileti delenit augue duis dolore teleoi feugait nulla dolor in hendrerit in vulputate consequat.Duis autem vel eum iriure dolor in hendrerit in vulputate.</p>
</section>

<section class="panel ipsum-two">
  <h2>LOREM <em>IPSUM</em></h2>
  <div class="rule"></div>
  <ul>
    <li><svg viewBox="0 0 12 10"><path d="M1 5 H10 M7 2 L10 5 L7 8" fill="none" stroke="#13206a" stroke-width="1.3"/></svg>Lorem ipsum dolor sit amet, consectetuer adipiscing elit, sed diam sit amet</li>
    <li><svg viewBox="0 0 12 10"><path d="M1 5 H10 M7 2 L10 5 L7 8" fill="none" stroke="#13206a" stroke-width="1.3"/></svg>Lorem ipsum dolor sit amet, consectetuer adipiscing elit</li>
    <li><svg viewBox="0 0 12 10"><path d="M1 5 H10 M7 2 L10 5 L7 8" fill="none" stroke="#13206a" stroke-width="1.3"/></svg>Lorem ipsum dolor sit amet, consectetuer adipiscing elit, sed diam</li>
    <li><svg viewBox="0 0 12 10"><path d="M1 5 H10 M7 2 L10 5 L7 8" fill="none" stroke="#13206a" stroke-width="1.3"/></svg>Lorem ipsum dolor sit amet, consectetuer adipiscing elit, sed diam sit amet</li>
    <li><svg viewBox="0 0 12 10"><path d="M1 5 H10 M7 2 L10 5 L7 8" fill="none" stroke="#13206a" stroke-width="1.3"/></svg>Lorem ipsum dolor sit amet, consectetuer adipiscing elit</li>
    <li><svg viewBox="0 0 12 10"><path d="M1 5 H10 M7 2 L10 5 L7 8" fill="none" stroke="#13206a" stroke-width="1.3"/></svg>Lorem ipsum dolor sit amet, consectetuer adipiscing elit, sed diam</li>
    <li><svg viewBox="0 0 12 10"><path d="M1 5 H10 M7 2 L10 5 L7 8" fill="none" stroke="#13206a" stroke-width="1.3"/></svg>Lorem ipsum dolor sit amet, consectetuer adipiscing elit</li>
  </ul>
</section>

<section class="photo tablet" role="img" aria-label="Finger selecting a choice on an electronic voting screen"></section>

<footer class="site-footer">
  <div class="social" aria-label="Social links"><span></span><span></span><span></span><span></span></div>
  <div class="brand"><i></i>LOCAL ELECTIONS</div>
  <a class="donate" href="#" aria-label="Donate with CoinDrift"><svg viewBox="0 0 16 16"><circle cx="10" cy="5" r="4" fill="none" stroke="#fff" stroke-width="1.4"/><path d="M1 14 L5 10 H10 L12 12" fill="none" stroke="#fff" stroke-width="1.4"/></svg>DONATE</a>
</footer>
<div class="copyright">Copyright © 2016 Local Elections. All Rights Reserved.</div>
</body>
</html>
```